Bluecrest Learning Corps by graduating students from college in two years

Based on the logo design, create stationary and business cards for
Dr. Venrel T Oskamp, CEO, (703) 482-1736
and Marisa Deltoft, Respresentative, (301) 647-2208
Address: 4719 Pellham Court, Brennick Falls, VA 22417
Incorporate elelments of the logo

Target Market(s)

USA

Font styles to use
Other font styles liked:
• match with the logo type style

```html
<!DOCTYPE html>
<html lang="en">
<head>
<meta charset="UTF-8">
<title>Bluecrest Learning Corps — Letterhead</title>
<link href="https://fonts.googleapis.com/css2?family=Arimo:wght@400;700&family=Mulish:wght@600;700&display=swap" rel="stylesheet">
<style>
  :root {
    --navy: #0f2060;
    --gold: #f8c52c;
    --ink: #555555;
    --rule: #4a4a4a;
    --paper: #ffffff;
    --backdrop: #e3e3e3;
  }
  * { margin: 0; padding: 0; box-sizing: border-box; }
  html, body {
    width: 1153px; height: 1200px; overflow: hidden;
    background: var(--backdrop);
  }
  .letterhead {
    position: absolute; left: 166px; top: 20px;
    width: 820px; height: 1160px;
    background: var(--paper);
    font-family: "Arimo", Arial, sans-serif;
    color: var(--ink);
  }
  .contact {
    position: absolute; top: 52px;
    line-height: 1.25;
  }
  .contact--left { left: 56px; }
  .contact--right { left: 654px; }
  .contact__name { color: var(--navy); font-weight: 700; font-size: 16.5px; }
  .contact__role { font-size: 13.5px; margin-top: 1px; }
  .contact__phone { font-size: 13.5px; margin-top: 4px; display: flex; align-items: center; gap: 3px; }
  .contact__phone svg { width: 12px; height: 10px; }
  .header-rule {
    position: absolute; top: 124px; height: 1.5px; background: var(--rule);
  }
  .header-rule--left { left: 56px; width: 290px; }
  .header-rule--right { left: 474px; width: 289px; }
  .brand-mark {
    position: absolute; left: 346px; top: 38px;
    width: 128px; height: 128px;
    display: flex; flex-direction: column; align-items: center; justify-content: center;
    gap: 6px; text-align: center;
  }
  .brand-mark__dot { width: 20px; height: 20px; border-radius: 50%; background: var(--gold); }
  .brand-mark__name {
    color: var(--navy); font-weight: 700; font-size: 14px; line-height: 1.15;
  }
  .salutation {
    position: absolute; left: 75px; top: 350px;
    font-family: "Mulish", Arial, sans-serif; font-weight: 700;
    font-size: 19px; color: var(--ink);
  }
  .letter-body {
    position: absolute; left: 73px; top: 408px; width: 676px;
    font-size: 14.2px; line-height: 16.8px;
  }
  .letter-body p + p { margin-top: 15px; }
  .closing {
    position: absolute; left: 75px; top: 758px;
    font-family: "Mulish", Arial, sans-serif; font-weight: 700; font-size: 11px;
  }
  .signature {
    position: absolute; left: 68px; top: 808px; width: 104px; height: 30px;
    background: linear-gradient(90deg, #d8d8d8, #ececec);
    border-radius: 4px;
  }
  .footer-band { position: absolute; left: 0; bottom: 0; width: 820px; height: 27px; }
  .footer-address {
    position: absolute; left: 482px; bottom: 5px;
    color: #ffffff; font-size: 13px;
  }
</style>
</head>
<body>
  <main class="letterhead">
    <header>
      <div class="contact contact--left">
        <div class="contact__name">Dr. Venrel T Oskamp</div>
        <div class="contact__role">CEO</div>
        <div class="contact__phone">
          <svg viewBox="0 0 12 10" aria-hidden="true"><path fill="#f8c52c" d="M1 3 Q6 -1 11 3 L10 4.5 L8 4 L8 3 Q6 2.2 4 3 L4 4 L2 4.5 Z M3 5 H9 L10.5 9.5 H1.5 Z"/></svg>
          (703) 482-1736
        </div>
      </div>
      <div class="header-rule header-rule--left"></div>
      <div class="brand-mark">
        <span class="brand-mark__dot"></span>
        <span class="brand-mark__name">Bluecrest<br>Learning Corps</span>
      </div>
      <div class="header-rule header-rule--right"></div>
      <div class="contact contact--right">
        <div class="contact__name">Marisa Deltoft</div>
        <div class="contact__role">Respresentative</div>
        <div class="contact__phone">
          <svg viewBox="0 0 12 10" aria-hidden="true"><path fill="#f8c52c" d="M1 3 Q6 -1 11 3 L10 4.5 L8 4 L8 3 Q6 2.2 4 3 L4 4 L2 4.5 Z M3 5 H9 L10.5 9.5 H1.5 Z"/></svg>
          (301) 647-2208
        </div>
      </div>
    </header>

    <h1 class="salutation">Dear Mr. Smith,</h1>

    <section class="letter-body">
      <p>Lorem ipsum dolor sit amet, consectetuer adipiscing elit, sed diam nonmmy nibh euismod tincidunt ut laor eet dolore magna aliquam erat volutpat. Ut wisi enim ad minim veniam, quis nostrud exerci tationmcorper suscipit lobortis nisl ut aliquip ex ea commodo consequat. Duis autem vel eum iriure dolor in hendrerit in vulputate velit esse molestie consequat, vel illum dolore eu feugiat</p>
      <p>Rorem ipsum dolor sit amet, consectetuer adipiscing elit, sed diam nonmmy nibh euismod tincidunt ut laor eet dolore magna aliquam erat volutpat. Ut wisi enim ad minim veniam, quis nostrud exerci tationmcorper suscipit lobortis nisl ut aliquip ex ea commodo consequat. Duis autem vel eum iriure dolor in hendrerit in vulputate velit esse molest</p>
      <p>Dorem ipsum dolor sit amet, consectetuer adipiscing elit, sed diam nonmmy nibh euismod tincidunt ut laor eet dolore magna aliquam erat volutpat. Ut wisi enim ad minim veniam, quis nostrud exerci tationmcorper suscipit lobortis nisl ut aliquip ex ea commodo consequat. Duis autem vel eum iriure dolor in hendrerit in suscipit lobortis nisl ut aliquip ex ea commodo consequat. Duis autem vel eum iriure dolor in hendrerit in vulputate velit esse molestie consequat, vel illum</p>
      <p>Sorem ipsum dolor sit amet, consectetuer adipiscing elit, sed diam nonmmy nibh euismod tincidunt ut laor eet dolore magna aliquam erat volutpat. Ut wisi enim ad minim veniam, quis nostrud exerci tationmcorper suscipit lobortis nisl ut aliquip ex ea commodo consequat. Duis autem vel eum iriure dolor in</p>
    </section>

    <div class="closing">Sincerely,</div>
    <div class="signature" role="img" aria-label="Handwritten signature"></div>

    <footer>
      <svg class="footer-band" viewBox="0 0 820 27" aria-hidden="true">
        <polygon points="0,14 437,14 428,27 0,27" fill="#f8c52c"/>
        <polygon points="459,0 820,0 820,27 437,27" fill="#0f2060"/>
      </svg>
      <div class="footer-address">4719 Pellham Court, Brennick Falls, VA 22417</div>
    </footer>
  </main>
</body>
</html>
```